kmvalerohub website

I need a new homepage design for my current website at www.KMValeroHub.com. I want someone to look at my current website and develop a more appealing homepage... right now the colors don't blend very well and it needs a facelift

Reason: This has been extended to September 10th

```html
<!DOCTYPE html>
<html lang="en">
<head>
<meta charset="utf-8">
<title>KM Valero – Home</title>
<link href="https://fonts.googleapis.com/css2?family=Oswald:wght@400;500&family=Open+Sans:wght@400;600&family=Great+Vibes&display=swap" rel="stylesheet">
<style>
:root{
  --pink:#e8388f;
  --pink-text:#e0398e;
  --green:#6a9e22;
  --green-light:#9cc43a;
  --green-dark:#4f7a16;
  --promo-green:#3f8a25;
  --black:#141414;
  --charcoal:#3b3b3b;
  --hero-bg:#cdc1b7;
  --gray-frame:#9a9a9a;
  --gray-panel:#ececec;
  --text:#333;
  --white:#fff;
  --teal:#1a8fb0;
  --red:#e8304a;
}
*{box-sizing:border-box;margin:0;padding:0}
html,body{width:798px;height:1200px;overflow:hidden}
body{position:relative;background:var(--white);font-family:"Open Sans",sans-serif;color:var(--text)}
.abs{position:absolute}
.topbar{left:0;top:0;width:798px;height:46px;background:var(--pink)}
.brand{left:122px;top:13px;color:var(--white);font-size:16px;font-weight:400;letter-spacing:1px}
.social{top:0;width:28px;height:36px;color:var(--white);font-size:7px;font-weight:600;text-align:center;padding-top:22px;border-radius:0 0 3px 3px}
.social.share{left:581px;background:#6d8fc8}
.social.follow{left:616px;background:#47c1d6}
.social.watch{left:650px;background:#d63a3a}
.greenband{left:0;top:46px;width:798px;height:276px;background:radial-gradient(ellipse at 45% 0%,var(--green-light) 0%,var(--green) 45%,var(--green-dark) 100%);border-bottom:2px solid var(--pink)}
.frame{left:114px;top:86px;width:570px;height:1064px;background:var(--gray-frame);border-top:4px solid #3f6612}
.page{left:120px;top:91px;width:558px;height:1059px;background:var(--white)}
.nav{left:120px;top:91px;width:558px;height:31px;background:linear-gradient(#2a2a2a,#0d0d0d);display:flex;font-family:"Oswald",sans-serif;font-size:8.5px;color:var(--white);text-transform:uppercase}
.nav span{padding:0 14px;line-height:31px}
.nav .active{background:var(--pink);padding:0 17px}
.hero{left:120px;top:122px;width:558px;height:262px;background:var(--hero-bg);border-bottom:3px solid var(--charcoal)}
.hero-photo{left:32px;top:8px;width:176px;height:251px;background:linear-gradient(90deg,#c9bbb0,#6a5e58 45%,#3c3533 60%,#c9bbb0)}
.hero-copy{left:232px;top:38px;width:250px;text-align:center}
.script{font-family:"Great Vibes",cursive;font-size:28px;color:var(--black);line-height:30px}
.h1{font-family:"Oswald",sans-serif;font-size:30px;color:var(--pink);line-height:38px}
.h2{font-family:"Oswald",sans-serif;font-size:25px;letter-spacing:1.5px;line-height:38px}
.h2 .p{color:#e167a8}.h2 .g{color:var(--green)}
.h3{font-family:"Oswald",sans-serif;font-size:30px;color:var(--charcoal);line-height:40px}
.arrow{width:14px;height:14px;top:137px}
.dots{left:257px;top:240px;display:flex;gap:10px}
.dot{width:7px;height:7px;border-radius:50%;border:1px solid #555}
.section-title{font-family:"Oswald",sans-serif;font-weight:400;font-size:13px;color:var(--pink-text);text-transform:uppercase;letter-spacing:.3px}
.about-photo{left:148px;top:462px;width:115px;height:130px;border:5px solid #e6e6e6;outline:1px solid #ccc;background:linear-gradient(135deg,#2a1c1a,#5a3a30 50%,#7a2b26)}
.about-text{left:286px;top:462px;width:378px;font-size:7.4px;line-height:14.9px;color:var(--text)}
.more{left:615px;top:579px;font-size:7.4px;color:var(--pink-text)}
.pager{top:627px;width:14px;height:14px;border-radius:50%;border:1px solid #ccc}
.card{top:650px;width:122px;height:124px;border:1px solid #d8d8d8;background:linear-gradient(#fff,#f6f6f6)}
.card.on{border-color:#f0a5c8;background:#fdf3f8}
.card .cover{left:36px;top:10px;width:50px;height:74px}
.card p{position:absolute;left:9px;top:90px;width:106px;font-size:7.2px;line-height:12.4px;color:var(--text)}
.card.on p{color:var(--pink-text)}
.report{left:120px;top:794px;width:558px;height:80px;background:var(--pink)}
.report h3{position:absolute;left:26px;top:13px;font-family:"Oswald",sans-serif;font-weight:400;font-size:13px;color:var(--white);letter-spacing:.5px}
.report p{position:absolute;left:26px;top:36px;width:280px;font-size:6.6px;line-height:17px;color:#fde2ef;text-transform:uppercase}
.field{width:142px;height:17px;background:var(--white);border:1px solid #ddd;border-radius:2px;font-size:6.3px;color:#999;padding:4px 7px}
.subscribe{left:458px;top:32px;width:65px;height:19px;background:linear-gradient(#7bb32c,#5a8c1a);color:var(--white);font-size:7px;text-align:center;line-height:19px}
.promo{left:120px;top:874px;width:558px;height:162px;background:linear-gradient(90deg,#eef8ef,#e4f5d7 60%,#f2f9e9)}
.promo .title{left:44px;top:20px;font-family:"Oswald",sans-serif;font-weight:500;font-size:28px;color:var(--teal);line-height:34px}
.promo .reset{left:44px;top:56px;font-family:"Oswald",sans-serif;font-weight:500;font-size:44px;color:var(--promo-green);line-height:52px;letter-spacing:4px}
.promo .tag{left:44px;top:122px;font-family:"Oswald",sans-serif;font-size:13px;color:var(--promo-green);line-height:16px}
.promo .avail{left:312px;top:122px;font-family:"Oswald",sans-serif;font-size:12px;color:var(--teal);line-height:16px}
.promo .by{left:160px;top:143px;font-size:9px;color:#5aa33a;line-height:12px}
.badge{left:320px;top:34px;width:76px;height:76px;border-radius:50%;background:var(--teal);color:var(--white);font-family:"Oswald",sans-serif;font-size:10.5px;line-height:13px;text-align:center;padding-top:19px}
.promo-cover{left:414px;top:8px;width:100px;height:138px;background:linear-gradient(160deg,#f3f7ef,#9bc46c 55%,#3e7a26);transform:rotate(6deg);box-shadow:2px 3px 6px rgba(0,0,0,.2)}
.seen{left:120px;top:1036px;width:558px;height:114px;background:var(--gray-panel)}
.seen .label{position:absolute;left:22px;top:19px;font-size:6.8px;color:var(--pink-text);text-transform:uppercase}
.logos{left:23px;top:38px;width:508px;height:49px;background:var(--white);display:flex;align-items:center;justify-content:space-around;font-family:"Oswald",sans-serif;font-size:16px;color:#2a2a2a}
.round{top:51px;width:24px;height:24px}
.footer{left:0;top:1150px;width:798px;height:50px;background:var(--black);color:var(--white);text-align:center;font-size:7px}
.footer .links{padding-top:11px}
.footer .copy{padding-top:13px;font-size:6px}
</style>
</head>
<body>
<div class="abs topbar"></div>
<div class="abs brand">KM Valero</div>
<div class="abs social share">Share</div>
<div class="abs social follow">Follow</div>
<div class="abs social watch">Watch</div>
<div class="abs greenband"></div>
<div class="abs frame"></div>
<div class="abs page"></div>

<nav class="abs nav"><span class="active">Home</span><span>Products</span><span>About</span><span>Blog</span><span>Forum</span><span>Media Room</span><span>Success Stories</span></nav>

<section class="abs hero">
  <div class="abs hero-photo" role="img" aria-label="Portrait of KM Valero standing in a grey halter dress"></div>
  <div class="abs hero-copy">
    <div class="script">Discover</div>
    <div class="h1">SECRETS TO A</div>
    <div class="h2"><span class="p">SLIMMER</span> <span class="g">SEXIER</span></div>
    <div class="h3">&amp; HEALTHIER YOU!</div>
  </div>
  <svg class="abs arrow" style="left:7px" viewBox="0 0 14 14"><circle cx="7" cy="7" r="7" fill="#666"/><path d="M8.5 4 5.5 7l3 3" stroke="#ddd" stroke-width="1.6" fill="none"/></svg>
  <svg class="abs arrow" style="left:537px" viewBox="0 0 14 14"><circle cx="7" cy="7" r="7" fill="#666"/><path d="M5.5 4l3 3-3 3" stroke="#ddd" stroke-width="1.6" fill="none"/></svg>
  <div class="abs dots"><span class="dot" style="background:var(--pink)"></span><span class="dot" style="background:var(--green)"></span><span class="dot" style="background:var(--pink)"></span></div>
</section>

<h2 class="abs section-title" style="left:136px;top:417px">About KM Valero</h2>
<div class="abs about-photo" role="img" aria-label="Photo of KM Valero seated in a black dress"></div>
<p class="abs about-text">KM Valero is a nutritionist and certified weight-loss expert, passionate relationship/life coach, and inspirational speaker. She has been featured on The Dawn Rivers Morning Show, The Calvin Brooks Show, The Lena Marsh Show, and The Andre Hollis Show. KM has made appearances on the NTV, VBX, CTN, BizNet and WaveTV Network television stations, as well as in the pages of Glow, Luster, Mind and Spirit, and Modern Home Digest. Since reclaiming her health, losing weight, and discovering a “second youth” in her forties, bestselling author KM Valero has become the voice of inspiration to women who want to lose weight, be healthy, and get their sexy back! KM Valero provides lifestyle solutions for losing weight, getting healthy, looking younger and improving your love life!</p>
<a class="abs more">Read More...</a>

<h2 class="abs section-title" style="left:139px;top:622px">Products</h2>
<span class="abs pager" style="left:633px"></span><span class="abs pager" style="left:651px"></span>

<div class="abs card on" style="left:145px"><div class="abs cover" role="img" aria-label="Book cover, 10-Day Fresh Greens Reset" style="background:linear-gradient(#eef6e8,#7dbb4a)"></div><p>The 10-Day Fresh Greens Reset</p></div>
<div class="abs card" style="left:278px"><div class="abs cover" role="img" aria-label="DVD set, Simple Steps to Slim Down" style="left:24px;width:74px;background:linear-gradient(#ddd,#b9a5b0 70%,#e05a9c)"></div><p>Simple Steps to Slim Down DVD</p></div>
<div class="abs card" style="left:413px"><div class="abs cover" role="img" aria-label="Book cover, 6 Ways to Trim Your Waist" style="background:linear-gradient(#f2f2f2,#d8505a 60%,#333)"></div><p>6 Ways to Trim Your Waist Without a Gym!</p></div>
<div class="abs card" style="left:547px"><div class="abs cover" role="img" aria-label="Book cover, Slim Down Without Strict Diets" style="background:linear-gradient(#f7d5e6,#e04a96 60%,#555)"></div><p>Slim Down Without Strict Diets or Workouts!</p></div>

<section class="abs report">
  <h3>FREE REPORT:</h3>
  <p>Just enter your name and email below to get instant access to this 30 page report absolutely free!</p>
  <div class="abs field" style="left:306px;top:19px">Name</div>
  <div class="abs field" style="left:306px;top:47px">Email Address</div>
  <div class="abs subscribe">SUBSCRIBE</div>
</section>

<section class="abs promo">
  <div class="abs title">10-DAY FRESH GREENS</div>
  <div class="abs reset">RESET</div>
  <div class="abs tag">LOSE WEIGHT. GET HEALTHY. FEEL ENERGIZED.</div>
  <div class="abs avail">Available Now</div>
  <div class="abs by">By KM Valero, #1 Bestselling Author, Nutritionist and Weight-Loss Expert</div>
  <div class="abs badge">LOSE UP TO<br>15 POUNDS<br>IN 10 DAYS!</div>
  <div class="abs promo-cover" role="img" aria-label="Book cover, 10-Day Fresh Greens Reset with a green drink"></div>
</section>

<section class="abs seen">
  <span class="label">As seen on...</span>
  <div class="abs logos"><span>OrbitAir</span><span>CTN</span><span>Luster.com</span><span>VBX</span><span>Beat 88</span><span>NTV</span></div>
  <svg class="abs round" style="left:6px" viewBox="0 0 24 24"><circle cx="12" cy="12" r="12" fill="#e8304a"/><path d="M14 7l-5 5 5 5" stroke="#fff" stroke-width="1.6" fill="none"/></svg>
  <svg class="abs round" style="left:525px" viewBox="0 0 24 24"><circle cx="12" cy="12" r="12" fill="#e8304a"/><path d="M10 7l5 5-5 5" stroke="#fff" stroke-width="1.6" fill="none"/></svg>
</section>

<footer class="abs footer">
  <div class="links">Privacy Policy &nbsp;|&nbsp; Terms of Use &nbsp;|&nbsp; Disclaimer</div>
  <div class="copy">Copyright © 2014. All Right Reserved.</div>
</footer>
</body>
</html>
```